Im want a website LIKE VRX's and FleetHollow.com's with product payment options like Trenzo's

I need a website LIKE VRX with a header made EXACTLY LIKE THAT OF FLEETHOLLOWS .

The front page photo should be like that of FLEETHOLLOW's webpage as well.

The name of the website will be called "M.K. (Caldera Key)".

We will be targeting ALL MARKETS in a small town in central Panama and charging businesses "listing fees" like a phone book does but also providing informational blogs, news, and other interesting activities.

THIS IS A MULTI PAGE WEBSITE

THIS IS WHERE VRX's website meets Brivelle/FleetHollow.

Once the layout is built I will tweak and modify, add information, and upload items for sale.

Here is a list of specific categories that should be listed out above the front page header image/search bar

-- Home -- News -- Travel -- Activities -- Shop & Dine -- Store -- More... --

These categories should be spread across the bottom of the page in three sections:

WHATS SO GREAT ABOUT (Caldera Key),
HAND PICKED TOURS
ACTIVITIES etc.

Also lets use www.Trenzo.example 's
"HOT DESTINATIONS"
"BEAT THE BEST PRICES IN BOQUETE"
"OCTOBERS INSIDER PICKS"
"TOP DESTINATIONS"
and spread them in four sections side-by-side near the bottom of the page.

Overall I would like to see the finished product to be something LIKE VRX's and FleetHollows.

WE NEED ONLINE PAYMENT OPTIONS LIKE BRIVELLE'S WEBSITE HAS

This will be a desktop website but should be very mobile friendly as well.

-rodmund

P.S. Good luck!

If it isn't already too late to change the website name, the name of the website should be "Caldera Key". Added Friday, October 9, 2015

What do you guys think the budget should be to win this? Added Saturday, October 10, 2015

www.palmorra.example is the most amazing simple site. Whoever can make me a replica with my specifications will win immediately!!!! Added Sunday, October 18, 2015

OMG www.palmorra.example is the bomb!So simple and elegant. Whoever can make me an EXACT REPLICA OF WWW.PALMORRA.EXAMPLE as my site with the specifications mentioned in my brief will take home the $825.00 immediately! Good luck amigos! Added Sunday, October 18, 2015

Does anybody know how to add recurring monthly billing options on this website? Added Sunday, October 18, 2015

ALL MARKETS

Product

Coded - Design and coding required

5+ page

• Coinvey payment options.
• I must be able to add and remove photos/text and video from the HTML files in the page.
• Be creative my friends, and may the odds be forever in your favor!
• I added some photos of a good layout for our page below.

```html
<!DOCTYPE html>
<html lang="en">
<head>
<meta charset="utf-8">
<title>Caldera Key</title>
<link href="https://fonts.googleapis.com/css2?family=Open+Sans:wght@400;600;700;800&display=swap" rel="stylesheet">
<style>
:root{
  --blue:#1ea6d8;
  --blue-dark:#1482b0;
  --orange:#f5821f;
  --ink:#333;
  --muted:#777;
  --light:#eeeeee;
  --footer:#2a2d30;
  --footer-bottom:#1f2123;
  --star:#f5a623;
}
*{box-sizing:border-box;margin:0;padding:0}
html,body{width:1200px;height:2504px;overflow:hidden}
body{font-family:"Open Sans",Arial,sans-serif;color:var(--ink);background:#fff;position:relative}
a{color:inherit;text-decoration:none}

/* hero + header */
.hero{position:absolute;left:0;top:0;width:1200px;height:600px;
  background:linear-gradient(180deg,#7cc3e8 0%,#a9d4e6 30%,#c9a67c 55%,#8b6a4a 75%,#2f7fa3 100%)}
.topbar{position:absolute;left:0;top:0;width:1200px;height:30px;background:rgba(10,50,80,.75);
  color:#fff;font-size:11px;display:flex;align-items:center;justify-content:space-between;padding:0 72px}
.topbar span{margin-right:18px}
.topbar .right span{margin:0 0 0 18px}
.masthead{position:absolute;left:0;top:30px;width:1200px;height:64px;background:rgba(10,70,110,.55);
  display:flex;align-items:center;justify-content:space-between;padding:0 72px}
.brand{color:#fff;font-size:28px;font-weight:700;letter-spacing:.3px}
.nav{display:flex;gap:26px;color:#fff;font-size:11px;font-weight:700;text-transform:uppercase}
.search-box{position:absolute;left:140px;top:272px;width:440px;height:96px;background:var(--orange);padding:14px 18px}
.search-box h2{color:#fff;font-size:19px;font-weight:700;text-align:center;letter-spacing:.5px;margin-bottom:12px}
.search-row{display:flex;height:34px}
.search-row .field{flex:1;background:#fff;font-size:11px;color:#999;display:flex;align-items:center;padding-left:10px}
.search-row .go{width:90px;background:var(--blue);color:#fff;font-size:12px;font-weight:700;display:flex;align-items:center;justify-content:center}
.dots{position:absolute;left:124px;top:516px;display:flex;gap:8px}
.dots i{width:10px;height:10px;border-radius:50%;background:rgba(255,255,255,.6)}
.dots i:first-child{background:#fff}

/* features strip */
.features{position:absolute;left:0;top:600px;width:1200px;height:112px;background:#fff;border-bottom:1px solid #e2e2e2;
  display:flex;align-items:center;padding:0 72px}
.features .tag{width:190px;height:76px;background:var(--blue);color:#fff;font-weight:700;font-size:15px;line-height:19px;
  display:flex;align-items:center;justify-content:center;text-align:center;margin-right:30px}
.feature{flex:1;text-align:center;border-left:1px solid #e6e6e6;height:70px}
.feature svg{display:block;margin:4px auto 6px}
.feature b{display:block;font-size:12px;color:var(--blue);text-transform:uppercase}
.feature small{font-size:11px;color:var(--muted)}

/* section titles */
.section-title{position:absolute;left:0;width:1200px;text-align:center;font-size:22px;font-weight:600;color:#444;text-transform:uppercase}
.section-title::after{content:"";display:block;width:60px;height:2px;background:var(--blue);margin:10px auto 0}

/* packages */
.packages{position:absolute;left:72px;top:812px;width:1056px;display:flex;gap:24px}
.package{flex:1}
.package .photo{height:176px}
.package h3{color:var(--blue);font-size:18px;font-weight:700;margin:12px 0 4px}
.rating{font-size:12px;color:var(--muted)}
.rating .stars{color:var(--star);letter-spacing:1px;margin-right:6px}
.package p{font-size:11px;color:var(--muted);line-height:16px;margin:6px 0 10px}
.price-row{display:flex;justify-content:space-between;align-items:flex-end}
.price small{display:block;font-size:10px;color:var(--muted)}
.price strong{font-size:26px;font-weight:700;color:#333}
.btn-blue{background:var(--blue);color:#fff;font-size:11px;font-weight:700;padding:9px 14px;text-transform:uppercase}

/* listings */
.listing-band{position:absolute;left:0;top:1212px;width:1200px;height:888px;background:var(--light)}
.tabs{position:absolute;left:0;top:1300px;width:1200px;display:flex;justify-content:center;gap:4px}
.tabs span{font-size:10px;font-weight:700;text-transform:uppercase;padding:7px 22px;background:#fff;color:#555}
.tabs .active{background:var(--orange);color:#fff}
.listings{position:absolute;left:72px;top:1372px;width:1056px;display:grid;grid-template-columns:repeat(4,1fr);column-gap:24px;row-gap:40px}
.listing .photo{height:120px}
.listing h4{color:var(--blue);font-size:15px;font-weight:600;margin:10px 0 3px}
.listing p{font-size:11px;color:var(--muted);line-height:16px;margin:6px 0}
.listing .more{font-size:11px;color:var(--orange);font-weight:600}

/* newsletter */
.signup{position:absolute;left:0;top:2100px;width:1200px;height:92px;background:var(--blue);display:flex;align-items:center;padding:0 72px;gap:40px}
.signup-block{flex:1;display:flex;align-items:center;gap:12px}
.signup-block h5{color:#fff;font-size:17px;font-weight:600;text-transform:uppercase;white-space:nowrap}
.signup-form{display:flex;height:32px;flex:1}
.signup-form .field{flex:1;background:#fff;font-size:11px;color:#999;display:flex;align-items:center;padding-left:10px}
.signup-form .btn{background:var(--orange);color:#fff;font-size:11px;font-weight:700;padding:0 16px;display:flex;align-items:center;text-transform:uppercase}
.signup-block.left h5{margin-right:10px}

/* footer */
.footer{position:absolute;left:0;top:2192px;width:1200px;height:260px;background:var(--footer);color:#aaa;padding:34px 72px 0;display:flex;gap:40px}
.footer .about{width:270px}
.footer .about .name{color:#fff;font-size:24px;font-weight:700;margin-bottom:12px}
.footer p{font-size:11px;line-height:18px}
.footer .col{width:140px}
.footer .col h6{color:#fff;font-size:13px;font-weight:700;text-transform:uppercase;margin-bottom:10px}
.footer .col li{list-style:none;font-size:11px;line-height:21px}
.footer .side{margin-left:auto;width:200px}
.mileage{display:flex;align-items:center;gap:8px;background:#fff;height:48px;padding:0 10px;color:#333;font-size:13px;font-weight:700;text-transform:uppercase}
.mileage i{width:28px;height:28px;border-radius:50%;background:var(--orange);display:block}
.side h6{color:#fff;font-size:13px;font-weight:700;text-transform:uppercase;margin:18px 0 10px}
.badges{display:flex;gap:8px}
.badges i{width:70px;height:24px;background:#555;display:block}
.social{display:flex;gap:8px;margin-top:12px}
.social i{width:22px;height:22px;border-radius:50%;background:var(--blue);display:block}
.copyright{position:absolute;left:0;top:2452px;width:1200px;height:52px;background:var(--footer-bottom);color:#888;font-size:11px;padding:0 72px;display:flex;align-items:center}
</style>
</head>
<body>

<div class="hero" role="img" aria-label="Smiling couple taking a selfie in front of a historic stone amphitheatre under a blue sky"></div>

<div class="topbar">
  <div class="left"><span>USD ($) ▾</span><span>English ▾</span></div>
  <div class="right"><span>Login / Register</span><span>My Cart</span><span>Help</span></div>
</div>

<header class="masthead">
  <div class="brand">Caldera Key</div>
  <nav class="nav">
    <a>Home</a><a>About</a><a>Guided Tours</a><a>Hotels/Hostels</a><a>Rental Vehicles</a><a>News &amp; Events</a><a>Contact</a>
  </nav>
</header>

<div class="search-box">
  <h2>LET THE ACTIVITIES BEGIN!</h2>
  <div class="search-row"><div class="field">Search for activities, tours, rentals, hotels...</div><div class="go">LET'S GO</div></div>
</div>
<div class="dots"><i></i><i></i><i></i><i></i></div>

<section class="features">
  <div class="tag">What So<br>Great About<br>Caldera Key</div>
  <div class="feature">
    <svg width="28" height="28" viewBox="0 0 28 28"><rect x="4" y="4" width="20" height="20" rx="3" fill="none" stroke="#1ea6d8" stroke-width="2.5"/><path d="M9 14l4 4 7-8" fill="none" stroke="#1ea6d8" stroke-width="2.5"/></svg>
    <b>Handpicked</b><small>Tours &amp; Activity</small></div>
  <div class="feature">
    <svg width="28" height="28" viewBox="0 0 28 28"><path d="M14 3l3.3 7 7.5.8-5.6 5 1.6 7.4L14 19.5l-6.8 3.7 1.6-7.4-5.6-5 7.5-.8z" fill="#1ea6d8"/></svg>
    <b>Verified</b><small>Reviews &amp; Photos</small></div>
  <div class="feature">
    <svg width="28" height="28" viewBox="0 0 28 28"><circle cx="14" cy="9" r="5" fill="#1ea6d8"/><path d="M4 25c0-6 4.5-9 10-9s10 3 10 9z" fill="#1ea6d8"/></svg>
    <b>VIP Corner</b><small>Access</small></div>
  <div class="feature">
    <svg width="28" height="28" viewBox="0 0 28 28"><path d="M3 14V4h10l12 12-10 10z" fill="#1ea6d8"/><circle cx="8.5" cy="9" r="2" fill="#fff"/></svg>
    <b>Low Prices</b><small>Guaranteed</small></div>
  <div class="feature">
    <svg width="28" height="28" viewBox="0 0 28 28"><path d="M5 17v-4a9 9 0 0 1 18 0v4" fill="none" stroke="#1ea6d8" stroke-width="2.5"/><rect x="3" y="15" width="5" height="8" rx="1.5" fill="#1ea6d8"/><rect x="20" y="15" width="5" height="8" rx="1.5" fill="#1ea6d8"/></svg>
    <b>24/7 Support</b><small>With Live Chat</small></div>
</section>

<h2 class="section-title" style="top:760px">Featured Packages</h2>
<section class="packages">
  <article class="package">
    <div class="photo" role="img" aria-label="Ancient stone ruins under a blue sky" style="background:linear-gradient(160deg,#6fb3e0,#c9b08a 60%,#8c7657)"></div>
    <h3>Popular Sightseeing</h3>
    <div class="rating"><span class="stars">★★★★★</span>335 Reviews</div>
    <p>Enjoy a full day around the key with a local guide, fresh lunch and easy transfers.</p>
    <div class="price-row"><div class="price"><small>Starting From</small><strong>$420.00</strong></div><a class="btn-blue">View Details</a></div>
  </article>
  <article class="package">
    <div class="photo" role="img" aria-label="Travellers on a guided walking tour" style="background:linear-gradient(160deg,#8fc6e6,#d6c2a4 55%,#a07c5c)"></div>
    <h3>Special Guided Tours</h3>
    <div class="rating"><span class="stars">★★★★★</span>324 Reviews</div>
    <p>Small groups, friendly guides and hidden spots few visitors ever get the chance to see.</p>
    <div class="price-row"><div class="price"><small>Starting From</small><strong>$420.00</strong></div><a class="btn-blue">View Details</a></div>
  </article>
  <article class="package">
    <div class="photo" role="img" aria-label="Historic hotel building with a tall tower" style="background:linear-gradient(160deg,#4f8fd0,#e0d6c4 55%,#b98d5f)"></div>
    <h3>Hotel/Hostels</h3>
    <div class="rating"><span class="stars">★★★★★</span>335 Reviews</div>
    <p>Cozy rooms and bright hostels close to the plaza, with breakfast and free parking.</p>
    <div class="price-row"><div class="price"><small>Starting From</small><strong>$420.00</strong></div><a class="btn-blue">View Details</a></div>
  </article>
  <article class="package">
    <div class="photo" role="img" aria-label="Row of parked scooters for rent" style="background:linear-gradient(160deg,#a7b7c4,#7d7f84 55%,#b03a2e)"></div>
    <h3>Rental Vehicles</h3>
    <div class="rating"><span class="stars">★★★★★</span>335 Reviews</div>
    <p>Scooters, bikes and small cars ready each morning for a day of easy exploring.</p>
    <div class="price-row"><div class="price"><small>Starting From</small><strong>$420.00</strong></div><a class="btn-blue">View Details</a></div>
  </article>
</section>

<div class="listing-band"></div>
<h2 class="section-title" style="top:1240px">Featured Listing</h2>
<div class="tabs"><span class="active">View All</span><span>Guided Tours</span><span>Hotels/Hostels</span><span>Rental Vehicles</span></div>

<section class="listings">
  <article class="listing"><div class="photo" role="img" aria-label="City skyline by the water" style="background:linear-gradient(160deg,#9ccbe8,#b9a894)"></div><h4>Fusce accumsan</h4><div class="rating"><span class="stars">★★★★★</span></div><p>Quiet rooms near the plaza with fresh breakfast and friendly local hosts.</p><a class="more">Read More »</a></article>
  <article class="listing"><div class="photo" role="img" aria-label="Boats on a calm harbour" style="background:linear-gradient(160deg,#5aa7d9,#2d6e9e)"></div><h4>Fusce accumsan</h4><div class="rating"><span class="stars">★★★★★</span></div><p>Quiet rooms near the plaza with fresh breakfast and friendly local hosts.</p><a class="more">Read More »</a></article>
  <article class="listing"><div class="photo" role="img" aria-label="Old town street with colourful buildings" style="background:linear-gradient(160deg,#c9a47a,#7e6a55)"></div><h4>Fusce accumsan</h4><div class="rating"><span class="stars">★★★★★</span></div><p>Quiet rooms near the plaza with fresh breakfast and friendly local hosts.</p><a class="more">Read More »</a></article>
  <article class="listing"><div class="photo" role="img" aria-label="Historic tower at sunset" style="background:linear-gradient(160deg,#e2b27d,#8b5a3a)"></div><h4>Fusce accumsan</h4><div class="rating"><span class="stars">★★★★★</span></div><p>Quiet rooms near the plaza with fresh breakfast and friendly local hosts.</p><a class="more">Read More »</a></article>
  <article class="listing"><div class="photo" role="img" aria-label="Group of friends on a guided tour" style="background:linear-gradient(160deg,#9fc3d9,#c0a080)"></div><h4>Fusce accumsan</h4><div class="rating"><span class="stars">★★★★★</span></div><p>Quiet rooms near the plaza with fresh breakfast and friendly local hosts.</p><a class="more">Read More »</a></article>
  <article class="listing"><div class="photo" role="img" aria-label="Traveller with a backpack on a mountain trail" style="background:linear-gradient(160deg,#7fa8c8,#5e7a52)"></div><h4>Fusce accumsan</h4><div class="rating"><span class="stars">★★★★★</span></div><p>Quiet rooms near the plaza with fresh breakfast and friendly local hosts.</p><a class="more">Read More »</a></article>
  <article class="listing"><div class="photo" role="img" aria-label="Bright hotel lobby interior" style="background:linear-gradient(160deg,#e6d5bd,#a68a68)"></div><h4>Fusce accumsan</h4><div class="rating"><span class="stars">★★★★★</span></div><p>Quiet rooms near the plaza with fresh breakfast and friendly local hosts.</p><a class="more">Read More »</a></article>
  <article class="listing"><div class="photo" role="img" aria-label="Red scooter parked on a street" style="background:linear-gradient(160deg,#c9c9c9,#b8342a)"></div><h4>Fusce accumsan</h4><div class="rating"><span class="stars">★★★★★</span></div><p>Quiet rooms near the plaza with fresh breakfast and friendly local hosts.</p><a class="more">Read More »</a></article>
</section>

<section class="signup">
  <div class="signup-block left">
    <svg width="26" height="20" viewBox="0 0 26 20"><rect x="1" y="1" width="24" height="18" fill="none" stroke="#fff" stroke-width="2"/><path d="M1 2l12 9 12-9" fill="none" stroke="#fff" stroke-width="2"/></svg>
    <h5>Newsletter Subscribe</h5>
    <div class="signup-form"><div class="field">Enter Email</div><div class="btn">Subscribe</div></div>
  </div>
  <div class="signup-block">
    <svg width="22" height="22" viewBox="0 0 22 22"><circle cx="9" cy="9" r="7" fill="none" stroke="#fff" stroke-width="2.5"/><path d="M14 14l6 6" stroke="#fff" stroke-width="2.5"/></svg>
    <h5>Find Your Next Activity</h5>
    <div class="signup-form"><div class="field">Enter Keyword</div><div class="btn">Search Now</div></div>
  </div>
</section>

<footer class="footer">
  <div class="about">
    <div class="name">Caldera Key</div>
    <p>Caldera Key brings together tours, stays, rentals and local news from our small town in central Panama, all in one place.</p>
  </div>
  <div class="col"><h6>Company</h6><ul><li>About Us</li><li>Our Team</li><li>Careers</li><li>Blog</li><li>Contact</li></ul></div>
  <div class="col"><h6>Support</h6><ul><li>Help Center</li><li>Privacy Policy</li><li>Terms of Use</li><li>FAQ</li><li>Site Map</li></ul></div>
  <div class="col"><h6>Partnership</h6><ul><li>Become a Partner</li><li>List Your Business</li><li>Affiliates</li><li>Advertise</li></ul></div>
  <div class="side">
    <div class="mileage"><i></i>Mileage Program</div>
    <h6>Mobile App</h6>
    <div class="badges"><i></i><i></i></div>
    <div class="social"><i></i><i></i><i></i><i></i><i></i><i></i></div>
  </div>
</footer>
<div class="copyright">© 2015 Caldera Key. All rights reserved.</div>

</body>
</html>
```